Home Staging Company needs business card design

We're a home staging company called Brightly Settled Home Staging. We would like a business card design that includes aqua and gray. Our current logo of house within chair is fine but I find we almost always use the logo in one color. I'll upload images of front and back of our current card and our logo. Note that we have dropped "Solutions" from our company name and don't want to include it on the card.

Target Market(s)

Realtors and homeowners - people interested in selling their homes

Contact Information for Business Card

Marisol Thistlewood
Brightly Settled Home Staging
757-555-0193
www.brightlysettled.com
marisol@brightlysettled.com

Font styles to use
Serif
Script

Requirements
Must have
• My logo and contact details
• UPDATE***
• I forgot to say that the company name should be included on the front of the card somehow.

```html
<!DOCTYPE html>
<html lang="en">
<head>
<meta charset="utf-8">
<title>Brightly Settled Home Staging – Business Card</title>
<link rel="stylesheet" href="https://fonts.googleapis.com/css2?family=Lora:wght@400;600&family=Playfair+Display+SC:wght@400&display=swap">
<style>
  :root {
    --backdrop: #1c1c1d;
    --charcoal: #424243;
    --aqua: #3bbbc6;
    --white: #ffffff;
  }
  * { margin: 0; padding: 0; box-sizing: border-box; }
  html, body { width: 1200px; height: 901px; overflow: hidden; background: var(--backdrop); }
  .canvas { position: relative; width: 1200px; height: 901px; }

  .card {
    position: absolute;
    width: 540px; height: 309px;
    border-radius: 20px;
    overflow: hidden;
    color: var(--white);
    box-shadow: 0 14px 30px rgba(0,0,0,.45);
  }
  .card svg.bands { position: absolute; inset: 0; width: 100%; height: 100%; }
  .card-front { left: 110px; top: 90px; background: var(--charcoal); }
  .card-back  { left: 550px; top: 470px; background: var(--aqua); }

  .band-aqua { fill: var(--aqua); }
  .band-charcoal { fill: var(--charcoal); }

  .holder { position: absolute; right: 38px; top: 36px; text-align: right; }
  .holder-name { font-family: "Playfair Display SC", serif; font-size: 23px; letter-spacing: .5px; line-height: 1.1; }
  .holder-role { font-family: "Lora", serif; font-size: 13px; }

  .contact { position: absolute; right: 38px; font-family: "Lora", serif; font-size: 13px; display: flex; align-items: center; gap: 8px; }
  .contact-phone { top: 120px; }
  .contact-email { top: 148px; }
  .contact svg { width: 18px; height: 18px; flex: none; }

  .brand-name {
    position: absolute;
    font-family: "Lora", serif;
    font-weight: 600;
    color: var(--white);
    line-height: 1.15;
    display: flex; align-items: center; gap: 12px;
  }
  .brand-name .mark { width: 14px; height: 14px; border-radius: 50%; background: var(--white); flex: none; }
  .card-front .brand-name { left: 34px; top: 118px; font-size: 24px; }
  .card-back .brand-name { left: 112px; top: 92px; font-size: 32px; }

  .website { position: absolute; font-family: "Lora", serif; font-size: 13px; display: flex; align-items: center; gap: 8px; }
  .card-front .website { left: 246px; top: 226px; }
  .card-back .website { left: 120px; top: 244px; }
  .website svg { width: 18px; height: 18px; flex: none; }
</style>
</head>
<body>
<main class="canvas">

  <section class="card card-front" aria-label="Card front">
    <svg class="bands" viewBox="0 0 540 309" aria-hidden="true">
      <path class="band-aqua" d="M200 204 H540 V207 H446 Q440 207 440 214 V250 Q440 262 428 262 H236 Q222 262 214 269 Q207 275 194 275 H0 V272 H192 Q202 272 202 262 Z"/>
    </svg>

    <div class="holder">
      <p class="holder-name">Marisol Thistlewood</p>
      <p class="holder-role">owner</p>
    </div>

    <p class="contact contact-phone">757-555-0193
      <svg viewBox="0 0 20 20" aria-hidden="true"><circle cx="10" cy="10" r="8.5" fill="none" stroke="#3bbbc6" stroke-width="1.5"/><path d="M7 6 l2 0 l.6 2.2 -1.1 .8 a5 5 0 0 0 2.5 2.5 l.8 -1.1 2.2 .6 0 2 a1 1 0 0 1 -1 1 a7 7 0 0 1 -7 -7 a1 1 0 0 1 1 -1z" fill="#3bbbc6"/></svg>
    </p>
    <p class="contact contact-email">marisol@brightlysettled.com
      <svg viewBox="0 0 20 20" aria-hidden="true"><circle cx="10" cy="10" r="8.5" fill="none" stroke="#3bbbc6" stroke-width="1.5"/><rect x="5.5" y="7" width="9" height="6.5" rx="1" fill="#3bbbc6"/><path d="M5.8 7.4 L10 10.6 L14.2 7.4" fill="none" stroke="#424243" stroke-width="1"/></svg>
    </p>

    <p class="brand-name"><span class="mark"></span><span>Brightly Settled<br>Home Staging</span></p>

    <p class="website">
      <svg viewBox="0 0 20 20" aria-hidden="true"><circle cx="10" cy="10" r="8.5" fill="none" stroke="#fff" stroke-width="1.5"/><circle cx="10" cy="10" r="4.5" fill="none" stroke="#fff" stroke-width="1"/><path d="M5.5 10 H14.5 M10 5.5 V14.5" stroke="#fff" stroke-width="1"/></svg>
      www.brightlysettled.com
    </p>
  </section>

  <section class="card card-back" aria-label="Card back">
    <svg class="bands" viewBox="0 0 540 309" aria-hidden="true">
      <path class="band-charcoal" d="M0 272 H330 Q346 272 352 258 L362 216 Q366 202 382 202 H540 V309 H0 Z"/>
    </svg>

    <p class="brand-name"><span class="mark"></span><span>Brightly Settled<br>Home Staging</span></p>

    <p class="website">
      <svg viewBox="0 0 20 20" aria-hidden="true"><circle cx="10" cy="10" r="8.5" fill="none" stroke="#fff" stroke-width="1.5"/><circle cx="10" cy="10" r="4.5" fill="none" stroke="#fff" stroke-width="1"/><path d="M5.5 10 H14.5 M10 5.5 V14.5" stroke="#fff" stroke-width="1"/></svg>
      www.brightlysettled.com
    </p>
  </section>

</main>
</body>
</html>
```